Heritage Hollow Business Cards

Require a business card design. <br/><br/>Needs to include logo (either round or long version) plus these details:<br/>Maya Torvell<br/>Heritage Hollow<br/>maya@kelvadtrading.com.au<br/>02 6481 7395<br/>PO Box Glenwarra NSW 2791<br/>www.heritagehollow.com.au<br/><br/>I need in an editable format so that I can create for multiple staff members. <br/><br/>

Target Market(s)

We are an online store selling renovation products to home owners are builders. Looking for a classic classy design.

Industry/Entity Type

Home And Garden

Contact Information for Business Card

Maya Torvell
Heritage Hollow
maya@kelvadtrading.com.au
02 6481 7395
PO Box Glenwarra NSW 2791
www.heritagehollow.com.au

Colors

Designer to choose colors to be used in the design.

Requirements
Must have
• Must include Logo.

```html
<!DOCTYPE html>
<html lang="en">
<head>
<meta charset="utf-8">
<title>Heritage Hollow Business Cards</title>
<link rel="stylesheet" href="https://fonts.googleapis.com/css2?family=Alike&family=Roboto:wght@300;400;500&display=swap">
<style>
  :root {
    --backdrop: #dcdde1;
    --card-dark: #0b0b0b;
    --card-light: #ececec;
    --ink: #1c1c1c;
    --ink-soft: #3a3a3a;
    --mark-faint: #5a5a5a;
    --mark-line: #4a4a4a;
  }
  * { margin: 0; padding: 0; box-sizing: border-box; }
  html, body { width: 1200px; height: 1200px; overflow: hidden; }
  body { background: var(--backdrop); position: relative; font-family: "Roboto", sans-serif; }

  .card {
    position: absolute;
    left: 271px;
    width: 659px;
    height: 378px;
    border-radius: 19px;
    overflow: hidden;
  }
  .card--front { top: 180px; background: var(--card-dark); }
  .card--back { top: 643px; background: var(--card-light); }

  /* Front: brand seal */
  .seal {
    position: absolute;
    left: 222px; top: 75px;
    width: 228px; height: 228px;
    border: 1px solid var(--mark-line);
    border-radius: 50%;
  }
  .seal__name {
    position: absolute;
    left: 0; right: 0; top: 95px;
    text-align: center;
    font-family: "Alike", serif;
    font-size: 30px;
    line-height: 32px;
    color: var(--mark-faint);
  }

  /* Back: brand line */
  .brand {
    position: absolute;
    left: 0; right: 0; top: 52px;
    display: flex;
    justify-content: center;
    align-items: center;
    gap: 16px;
  }
  .brand__dot {
    width: 62px; height: 62px;
    border: 1.5px solid var(--ink);
    border-radius: 50%;
  }
  .brand__name {
    font-family: "Alike", serif;
    font-size: 42px;
    color: var(--ink);
  }

  .holder {
    position: absolute;
    left: 0; right: 0; top: 252px;
    text-align: center;
    font-family: "Alike", serif;
    font-size: 30px;
    letter-spacing: 0.5px;
    color: var(--ink);
  }

  .details {
    position: absolute;
    top: 307px;
    left: 0; right: 0;
    height: 52px;
  }
  .details__company {
    position: absolute;
    right: 344px; top: 10px;
    text-align: right;
    white-space: nowrap;
  }
  .company__name { font-size: 15.5px; font-weight: 500; color: var(--ink); letter-spacing: 0.2px; }
  .company__address { font-size: 11.5px; font-weight: 400; color: var(--ink-soft); margin-top: 4px; letter-spacing: 0.3px; }
  .details__rule {
    position: absolute;
    left: 330px; top: 0;
    width: 1px; height: 52px;
    background: var(--ink);
  }
  .details__contacts {
    position: absolute;
    left: 344px; top: -2px;
    list-style: none;
  }
  .contact {
    display: flex;
    align-items: center;
    gap: 4px;
    font-size: 12.2px;
    font-weight: 300;
    color: var(--ink);
    height: 18.5px;
    white-space: nowrap;
  }
  .contact svg { width: 11px; height: 11px; flex: none; }
  .contact strong { font-weight: 500; }
</style>
</head>
<body>

  <section class="card card--front" aria-label="Card front">
    <div class="seal">
      <div class="seal__name">Heritage<br>Hollow</div>
    </div>
  </section>

  <section class="card card--back" aria-label="Card back">
    <div class="brand">
      <span class="brand__dot"></span>
      <span class="brand__name">Heritage Hollow</span>
    </div>

    <h1 class="holder">MAYA TORVELL</h1>

    <div class="details">
      <div class="details__company">
        <div class="company__name">HERITAGE HOLLOW</div>
        <div class="company__address">PO Box Glenwarra NSW 2791</div>
      </div>
      <div class="details__rule"></div>
      <ul class="details__contacts">
        <li class="contact">
          <svg viewBox="0 0 24 24" aria-hidden="true"><path fill="#1c1c1c" d="M6.6 10.8c1.4 2.8 3.8 5.1 6.6 6.6l2.2-2.2c.3-.3.7-.4 1-.2 1.1.4 2.3.6 3.6.6.6 0 1 .4 1 1V20c0 .6-.4 1-1 1C10.6 21 3 13.4 3 4c0-.6.4-1 1-1h3.5c.6 0 1 .4 1 1 0 1.3.2 2.5.6 3.6.1.3 0 .7-.2 1l-2.3 2.2z"/></svg>
          02 6481 7395
        </li>
        <li class="contact">
          <svg viewBox="0 0 24 24" aria-hidden="true"><rect x="2" y="5" width="20" height="14" rx="2" fill="none" stroke="#1c1c1c" stroke-width="2.4"/><path d="M2.5 6l9.5 7 9.5-7" fill="none" stroke="#1c1c1c" stroke-width="2.4"/></svg>
          maya@kelvadtrading.com.au
        </li>
        <li class="contact">
          <svg viewBox="0 0 24 24" aria-hidden="true"><circle cx="12" cy="12" r="9.5" fill="none" stroke="#1c1c1c" stroke-width="2.2"/><ellipse cx="12" cy="12" rx="4" ry="9.5" fill="none" stroke="#1c1c1c" stroke-width="2"/><path d="M2.5 12h19M4 7h16M4 17h16" stroke="#1c1c1c" stroke-width="1.8"/></svg>
          <span>www.<strong>heritagehollow</strong>.com.au</span>
        </li>
      </ul>
    </div>
  </section>

</body>
</html>
```